Bramblewood Joinery Website

My client Bramblewood Joinery is looking for a redesign for a Word Press Website. Their current site is at www.bramblewoodjoinery.example They are a custom cabinet company, but also create bathroom, living room, bar and entertainment and bedroom cabinets too. They would like a design that emulates the master craftsman work they do yet a contemporary style.

Their current site was designed using Flash elements.

Target Market(s)

Home owners and builders of high end homes

Industry/Entity Type

Entertainment

Font styles to use
Serif
Decorative

Requirements
Must have
• Must show their work and logo using a contemporary style.
Nice to have
• Sliders that showcase their projects.

```html
<!DOCTYPE html>
<html lang="en">
<head>
<meta charset="utf-8">
<title>Bramblewood Joinery</title>
<link href="https://fonts.googleapis.com/css2?family=Lato:wght@400;700&family=Mulish:ital,wght@0,300;0,400;0,500;1,300;1,400&display=swap" rel="stylesheet">
<style>
:root{
  --wood-light:#f2d3a2;
  --wood-mid:#e3b67b;
  --wood-dark:#c99556;
  --band:#6f5a42;
  --cream:#f6efe2;
  --green:#2fa73a;
  --green-dark:#268f30;
  --text:#6a6460;
  --heading:#1e1e1e;
  --nav-bg:rgba(90,70,50,.75);
  --white:#ffffff;
  --dash:#b8b2a8;
}
*{margin:0;padding:0;box-sizing:border-box}
html,body{width:1200px;height:1171px;overflow:hidden}
body{position:relative;background:var(--cream);font-family:"Mulish",sans-serif;color:var(--text)}
.wood{position:absolute;left:0;top:0;width:1200px;height:528px;
  background:repeating-linear-gradient(90deg,var(--wood-light) 0 40px,var(--wood-mid) 40px 44px,#edc48d 44px 88px,var(--wood-dark) 88px 90px,var(--wood-light) 90px 130px);}
.band{position:absolute;left:0;top:528px;width:1200px;height:38px;background:var(--band)}
.brand{position:absolute;left:112px;top:12px;display:flex;align-items:center;gap:10px}
.brand-dot{width:40px;height:40px;border-radius:50%;background:var(--green)}
.brand-name{font-family:"Lato",sans-serif;font-weight:700;font-size:22px;color:var(--heading);width:130px;line-height:1.1}
.contact{position:absolute;right:110px;top:8px;font-family:"Lato",sans-serif;font-size:19px;color:#2a2a2a}
.contact-row{display:flex;align-items:center;gap:8px;height:38px;justify-content:flex-end}
.contact-row svg{width:28px;height:28px}
.nav{position:absolute;left:283px;top:88px;width:807px;height:51px;background:var(--nav-bg);border-radius:10px;border-bottom:2px solid var(--green);display:flex;align-items:center;justify-content:space-around;padding:0 8px}
.nav a{color:var(--white);text-decoration:none;font-size:13.5px}
.slider{position:absolute;left:110px;top:172px;width:980px;height:346px;background:rgba(255,255,255,.5);padding:6px}
.slide-photo{width:968px;height:338px;background:linear-gradient(100deg,#6d6a66 0%,#b9a58d 45%,#d8cfc1 70%,#8d7a66 100%)}
.slide-caption{position:absolute;left:6px;top:6px;width:321px;height:338px;background:rgba(40,40,40,.55);text-align:center}
.pager{position:absolute;left:19px;top:18px;display:flex;gap:8px;color:var(--white);font-size:14px}
.pager span{width:26px;height:26px;line-height:26px;text-align:center}
.pager .on{background:#111;border-radius:50%}
.slide-title{position:absolute;left:0;top:64px;width:321px;font-style:italic;font-weight:300;font-size:35px;line-height:68px;color:var(--white)}
.slide-more{position:absolute;left:200px;top:264px;font-style:italic;font-size:14px;color:var(--green)}
.services{position:absolute;left:111px;top:519px;width:978px;height:85px;background:repeating-linear-gradient(135deg,var(--green) 0 3px,var(--green-dark) 3px 4px);display:flex;box-shadow:0 6px 6px -4px rgba(0,0,0,.3)}
.service{flex:1;display:flex;align-items:center;gap:22px;padding-left:28px;color:var(--white);border-right:1px solid rgba(255,255,255,.25)}
.service:last-child{border-right:none}
.service svg{width:54px;height:54px}
.service h3{font-weight:400;font-size:25px;font-family:"Mulish",sans-serif}
.service p{font-size:13px;margin-top:4px}
.about-photo{position:absolute;left:110px;top:651px;width:182px;height:141px;background:#c4c2bf;padding:6px 7px}
.about-photo div{width:100%;height:100%;background:linear-gradient(120deg,#5a5550,#b4a89a 55%,#7a5f45)}
.about{position:absolute;left:314px;top:645px;width:780px}
.about h2{font-weight:400;font-size:26px;color:var(--green)}
.about p{font-size:15px;line-height:28px;margin-top:6px}
.about a{color:var(--heading);text-decoration:none}
.rule{position:absolute;left:115px;top:825px;width:1041px;border-top:1px dashed var(--dash)}
.col{position:absolute;top:850px;height:255px}
.col h4{font-weight:400;font-size:20px;color:var(--heading);margin-top:4px}
.col p{font-size:13px;line-height:24px;margin-top:8px}
.col .more{position:absolute;right:34px;top:180px;font-style:italic;font-size:13.5px;color:var(--heading)}
.divider{border-left:2px dashed #ccc6bc}
.video{width:292px;height:131px;margin-top:10px;background:linear-gradient(110deg,#6c5638,#b98c55 50%,#3e3428);position:relative}
.video svg{position:absolute;left:111px;top:30px}
.footer-rule{position:absolute;left:0;top:1116px;width:1200px;border-top:1px dashed var(--dash)}
.footer{position:absolute;left:112px;top:1134px;width:977px;display:flex;justify-content:space-between;font-size:14px}
.footer span.sep{margin:0 10px}
</style>
</head>
<body>
<div class="wood"></div>
<div class="band"></div>

<header>
  <div class="brand"><span class="brand-dot"></span><span class="brand-name">Bramblewood Joinery</span></div>
  <div class="contact">
    <div class="contact-row"><svg viewBox="0 0 28 28"><circle cx="14" cy="14" r="13" fill="none" stroke="#8a7a66" stroke-width="1.5"/><path d="M9 8l3 0 1 4-2 1a8 8 0 0 0 4 4l1-2 4 1 0 3c-7 0-11-4-11-11z" fill="#8a7a66"/></svg>123 456 789</div>
    <div class="contact-row"><svg viewBox="0 0 28 28"><circle cx="14" cy="14" r="13" fill="none" stroke="#8a7a66" stroke-width="1.5"/><rect x="8" y="10" width="12" height="8" fill="none" stroke="#8a7a66" stroke-width="1.5"/><path d="M8 10l6 5 6-5" fill="none" stroke="#8a7a66" stroke-width="1.5"/></svg>info@bramblewoodjoinery.example</div>
  </div>
  <nav class="nav">
    <a href="#">Home</a><a href="#">Who We Are</a><a href="#">Getting Started</a><a href="#">Contact Us</a><a href="#">Customer Experience</a><a href="#">Professional</a><a href="#">Portfolio</a><a href="#">Cabinet Hardware</a>
  </nav>
</header>

<section class="slider">
  <div class="slide-photo" role="img" aria-label="Photo of a white custom kitchen with tiled backsplash and range hood"></div>
  <div class="slide-caption">
    <div class="pager"><span class="on">1</span><span>2</span><span>3</span></div>
    <div class="slide-title">Lorem ipsum<br>dolorsit amet,<br>consectetur</div>
    <div class="slide-more">read more &gt;&gt;</div>
  </div>
</section>

<section class="services">
  <div class="service">
    <svg viewBox="0 0 54 54"><circle cx="27" cy="27" r="26" fill="#111"/><circle cx="27" cy="27" r="9" fill="#fff"/><rect x="13" y="18" width="2" height="18" fill="#fff"/><rect x="39" y="18" width="2" height="18" fill="#fff"/></svg>
    <div><h3>KITCHEN</h3><p>Lorem Ipsum dolor sit amet</p></div>
  </div>
  <div class="service">
    <svg viewBox="0 0 54 54"><circle cx="27" cy="27" r="26" fill="#111"/><path d="M12 24h30v4a8 8 0 0 1-8 8H20a8 8 0 0 1-8-8z" fill="#fff"/><rect x="18" y="36" width="2" height="4" fill="#fff"/><rect x="34" y="36" width="2" height="4" fill="#fff"/></svg>
    <div><h3>BATH</h3><p>Lorem Ipsum dolor sit amet</p></div>
  </div>
  <div class="service">
    <svg viewBox="0 0 54 54"><circle cx="27" cy="27" r="26" fill="#111"/><rect x="21" y="12" width="12" height="16" rx="3" fill="#fff"/><rect x="18" y="29" width="18" height="4" fill="#fff"/><rect x="26" y="33" width="2" height="7" fill="#fff"/><rect x="19" y="40" width="16" height="2" fill="#fff"/></svg>
    <div><h3>OFFICE</h3><p>Lorem Ipsum dolor sit amet</p></div>
  </div>
</section>

<section>
  <div class="about-photo"><div role="img" aria-label="Photo of kitchen cabinets with built-in oven"></div></div>
  <div class="about">
    <h2>Who We Are</h2>
    <p>Lorem ipsum dolor sit amet, consectetur adipiscing elit, sed do eiusmod tempor incididunt ut labore et dolore magna aliqua. Ut enim ad minim veniam, quis nostrud exercitation ullamco laboris nisi ut aliquip ex ea commodo consequat. Duis aute irure dolor in reprehenderit in voluptate velit esse cillum dolore eu fugiat nulla<br><a href="#">read more &gt;&gt;</a></p>
  </div>
</section>

<div class="rule"></div>

<section>
  <div class="col" style="left:111px;width:300px">
    <h4>Watch Our Video</h4>
    <p>At Bramblewood Joinery, we've been designing and manufacturing the Midwest's finest custom cabinets and fixtures since 1966.</p>
    <div class="video" role="img" aria-label="Video still of a wooden kitchen">
      <svg width="70" height="70" viewBox="0 0 70 70"><circle cx="35" cy="35" r="31" fill="none" stroke="rgba(255,255,255,.5)" stroke-width="6"/><path d="M27 21l20 14-20 14z" fill="rgba(255,255,255,.5)"/></svg>
    </div>
  </div>
  <div class="col divider" style="left:439px;width:320px;padding-left:18px">
    <h4>Lorem Ipsum</h4>
    <p>Lorem ipsum dolor sit amet, consectetur adipiscing elit, sed do eiusmod tempor incididunt ut labore et dolore magna aliqua. Ut enim ad minim veniam, quis nostrud exercitation ullamco laboris nisi ut aliquip ex</p>
    <span class="more">read more</span>
  </div>
  <div class="col divider" style="left:757px;width:340px;padding-left:24px">
    <h4>Consectetur</h4>
    <p>Lorem ipsum dolor sit amet, consectetur adipiscing elit, sed do eiusmod tempor incididunt ut labore et dolore magna aliqua. Ut enim ad minim veniam, quis nostrud exercitation ullamco laboris nisi ut aliquip ex ea commodo consequat.</p>
    <span class="more" style="right:48px">read more</span>
  </div>
</section>

<div class="footer-rule"></div>
<footer class="footer">
  <span>© 2015 bramblewoodjoinery.example. All Right Reserved.</span>
  <span>Terms<span class="sep">I</span>Privacy Policy</span>
</footer>
</body>
</html>
```